Business Card Design and Logo Needed

I need Business Cards and a Logo for my website and public speaking business which can be found at: www.corvina-lett.example

I'm looking for creative and unique ideas. Some business cards I've found online that I like can be found at:
http://gigbarrow.example/general/18-smokin-hot-business-card-designs/

and at

http://www.plumquarry.example/2009/04/50-creative-business-cards-of-50-graphic-designers/

```html
<!DOCTYPE html>
<html lang="en">
<head>
<meta charset="utf-8">
<title>Corvina Lett — Business Card</title>
<link href="https://fonts.googleapis.com/css2?family=Orbitron:wght@500&family=Sacramento&display=swap" rel="stylesheet">
<style>
  :root {
    --page-bg: #ffffff;
    --card-bg: #2a1013;
    --accent: #6ea51c;
  }
  html, body {
    margin: 0;
    padding: 0;
    width: 1200px;
    height: 900px;
    overflow: hidden;
    background: var(--page-bg);
  }
  .canvas {
    position: relative;
    width: 1200px;
    height: 900px;
  }
  .card {
    position: absolute;
    left: 240px;
    width: 754px;
    height: 416px;
    border-radius: 60px;
    background: var(--card-bg);
    color: var(--accent);
  }
  .card--front { top: 20px; }
  .card--back { top: 450px; height: 418px; }

  .brand-mark {
    position: absolute;
    left: 20px;
    top: 60px;
    width: 290px;
    height: 300px;
    display: flex;
    flex-direction: column;
    align-items: center;
    justify-content: center;
    gap: 22px;
  }
  .brand-mark__dot {
    width: 130px;
    height: 130px;
    border-radius: 50%;
    background: var(--accent);
  }
  .brand-mark__name {
    font-family: "Orbitron", sans-serif;
    font-weight: 500;
    font-size: 13px;
    letter-spacing: 4px;
    text-transform: uppercase;
    white-space: nowrap;
  }

  .identity {
    position: absolute;
    left: 330px;
    top: 160px;
    width: 360px;
    text-align: center;
  }
  .identity__name {
    margin: 0;
    font-family: "Sacramento", cursive;
    font-weight: 400;
    font-size: 58px;
    line-height: 1;
    letter-spacing: 3px;
  }
  .identity__role {
    margin: 8px 0 0;
    font-family: "Orbitron", sans-serif;
    font-weight: 500;
    font-size: 9px;
    letter-spacing: 2px;
    text-transform: uppercase;
  }

  .contact {
    position: absolute;
    left: 285px;
    top: 348px;
    width: 450px;
    text-align: center;
    font-family: "Orbitron", sans-serif;
    font-weight: 500;
    font-size: 9px;
    letter-spacing: 1px;
    line-height: 18px;
    text-transform: uppercase;
    white-space: nowrap;
  }
  .contact p { margin: 0; }

  .tagline {
    position: absolute;
    left: 0;
    right: 0;
    top: 200px;
    margin: 0;
    text-align: center;
    font-family: "Orbitron", sans-serif;
    font-weight: 500;
    font-size: 12px;
    letter-spacing: 6px;
    text-transform: uppercase;
  }
</style>
</head>
<body>
<main class="canvas">
  <section class="card card--front" aria-label="Business card front">
    <div class="brand-mark" aria-label="Corvina Lett">
      <span class="brand-mark__dot"></span>
      <span class="brand-mark__name">Corvina Lett</span>
    </div>
    <div class="identity">
      <h1 class="identity__name">Corvina Lett</h1>
      <p class="identity__role">Speaker, Philanthropist, Author</p>
    </div>
    <div class="contact">
      <p>Phone: 07700900187 &bull; E-mail: info@corvina-lett.example</p>
      <p>www.corvina-lett.example</p>
    </div>
  </section>

  <section class="card card--back" aria-label="Business card back">
    <p class="tagline">Wonder. Explore. Dream. Achieve.</p>
  </section>
</main>
</body>
</html>
```